IT Company requires new Business Card design.

Over the years we have had a few different business card designs. We are now due for new cards across the board for all staff. We felt this would be a good time to start fresh with a new design. Our traditional card simply had our details on the front, and a list of services on the back. We don't particularly need the list of services, we have had cards where the only thing on the rear of the card was our logo.
Feel free to be creative, we would like our tag line "Complete IT Management" to appear at some point, doesn't necessarily have to be with the logo.
I have attached samples and drafts of various previous cards we have used over the years.

```html
<!DOCTYPE html>
<html lang="en">
<head>
<meta charset="utf-8">
<title>Harbor Systems – Business Card</title>
<link rel="stylesheet" href="https://fonts.googleapis.com/css2?family=Open+Sans:wght@400;600;700;800&display=swap">
<style>
  :root {
    --page-bg: #e6e3df;
    --card-dark: #2e2e2e;
    --card-mid: #4a4a4a;
    --card-light: #5c5c5c;
    --text-white: #ffffff;
    --text-soft: #e8e8e8;
    --rule: #9a9a9a;
    --mark-grey: #8c8c8c;
    --icon: #f2f2f2;
  }
  html, body {
    margin: 0;
    padding: 0;
    width: 1056px;
    height: 1200px;
    overflow: hidden;
    background: var(--page-bg);
    font-family: "Open Sans", Arial, sans-serif;
  }
  .canvas {
    position: relative;
    width: 1056px;
    height: 1200px;
  }
  .card {
    position: absolute;
    left: 78px;
    width: 900px;
    height: 514px;
    background:
      radial-gradient(ellipse 60% 55% at 50% 42%, var(--card-light) 0%, var(--card-mid) 45%, var(--card-dark) 100%);
    box-shadow: 0 6px 16px rgba(0,0,0,0.25);
    color: var(--text-soft);
    overflow: hidden;
  }
  .card--front { top: 62px; }
  .card--back { top: 624px; }

  /* front: brand lockup */
  .brand {
    position: absolute;
    left: 60px;
    top: 44px;
    display: flex;
    align-items: center;
    gap: 26px;
  }
  .brand__square {
    width: 104px;
    height: 104px;
    background: var(--mark-grey);
  }
  .brand__name {
    font-weight: 800;
    color: var(--text-white);
    font-size: 52px;
    line-height: 0.95;
    letter-spacing: 0.5px;
    text-transform: uppercase;
  }
  .brand__name span { display: block; }
  .brand__name span + span { font-size: 38px; margin-top: 4px; }
  .tagline {
    position: absolute;
    left: 190px;
    top: 178px;
    font-size: 15px;
    font-weight: 600;
    letter-spacing: 5px;
    color: var(--text-white);
    text-transform: uppercase;
  }

  /* front: person */
  .person {
    position: absolute;
    left: 60px;
    top: 285px;
  }
  .person__name {
    font-size: 26px;
    font-weight: 700;
    color: var(--text-white);
    margin: 0;
    line-height: 1.2;
  }
  .person__role {
    font-size: 21px;
    margin: 2px 0 0;
  }
  .website {
    font-size: 21px;
    color: var(--text-soft);
  }
  .website strong { font-weight: 700; color: var(--text-white); }
  .card--front .website {
    position: absolute;
    left: 60px;
    top: 452px;
  }

  .divider {
    position: absolute;
    left: 449px;
    top: 284px;
    width: 2px;
    height: 228px;
    background: var(--rule);
  }

  /* front: contacts */
  .contacts {
    position: absolute;
    left: 468px;
    top: 281px;
    margin: 0;
    padding: 0;
    list-style: none;
    font-size: 21px;
  }
  .contacts li {
    display: flex;
    align-items: center;
    height: 36px;
  }
  .contacts svg {
    width: 22px;
    height: 22px;
    margin-right: 11px;
    fill: var(--icon);
    flex: none;
  }
  .address {
    position: absolute;
    left: 468px;
    top: 440px;
    font-size: 21px;
    line-height: 31px;
    font-style: normal;
  }

  /* back */
  .back-brand {
    position: absolute;
    left: 0;
    right: 0;
    top: 150px;
    display: flex;
    justify-content: center;
    align-items: center;
    gap: 24px;
  }
  .back-brand .brand__square {
    width: 130px;
    height: 130px;
  }
  .back-brand .brand__name { font-size: 64px; }
  .back-brand .brand__name span + span { font-size: 47px; }
  .card--back .website {
    position: absolute;
    left: 0;
    right: 0;
    top: 460px;
    text-align: center;
    font-size: 24px;
  }
</style>
</head>
<body>
<main class="canvas">

  <section class="card card--front" aria-label="Business card front">
    <div class="brand">
      <div class="brand__square"></div>
      <div class="brand__name"><span>Harbor</span><span>Systems</span></div>
    </div>
    <div class="tagline">Complete IT Management</div>

    <div class="person">
      <p class="person__name">Daniel Reeve</p>
      <p class="person__role">Operation Manager</p>
    </div>
    <div class="website">www.<strong>harborsystems</strong>.com.au</div>

    <div class="divider"></div>

    <ul class="contacts">
      <li>
        <svg viewBox="0 0 24 24" aria-hidden="true"><path d="M12 1a11 11 0 1 0 0 22a11 11 0 0 0 0-22zm0 2a9 9 0 1 1 0 18a9 9 0 0 1 0-18z"/><path d="M8.2 6.5l2 2.2-1 1.4c.8 1.7 2 2.9 3.7 3.7l1.4-1 2.2 2-1.2 1.8c-3.8-.5-7.1-3.8-7.6-7.6z"/></svg>
        08 9356 4120
      </li>
      <li>
        <svg viewBox="0 0 24 24" aria-hidden="true"><path d="M7 2h10a1 1 0 0 1 1 1v18a1 1 0 0 1-1 1H7a1 1 0 0 1-1-1V3a1 1 0 0 1 1-1zm1 2v7h8V4zm0 9v2h2v-2zm3 0v2h2v-2zm3 0v2h2v-2zm-6 3v2h2v-2zm3 0v2h2v-2zm3 0v2h2v-2z"/></svg>
        0412 908 776
      </li>
      <li>
        <svg viewBox="0 0 24 24" aria-hidden="true"><path d="M7 3h8l2 2v5H7zM3 11h18a1 1 0 0 1 1 1v8H2v-8a1 1 0 0 1 1-1zm3 3v2h12v-2z"/></svg>
        08 9356 4120
      </li>
      <li>
        <svg viewBox="0 0 24 24" aria-hidden="true"><path d="M12 2l10 7v12H2V9zm0 2.4L4.5 9.6 12 14.5l7.5-4.9zM4 11.5V19h16v-7.5l-8 5.2z"/></svg>
        daniel@harborsystems.com.au
      </li>
    </ul>

    <address class="address">
      Unit 4 18 Marlow Road<br>
      Bibra Lake WA 6163
    </address>
  </section>

  <section class="card card--back" aria-label="Business card back">
    <div class="back-brand">
      <div class="brand__square"></div>
      <div class="brand__name"><span>Harbor</span><span>Systems</span></div>
    </div>
    <div class="website">www.<strong>harborsystems</strong>.com.au</div>
  </section>

</main>
</body>
</html>
```